Business Cards

Need business card design that I can update for new employees and details. Needs to incorporate our logo, be bright and fun (in line with tourism and holidays)
Would like a Map of Western Australia on the front with locations all the caravan parks we own (just purchased Tom Price so please include that as well as others listed on our website).
Target Market(s)
Famillies
Contact Information for Business Card
5 Cards -
Neil Perrow (Director) e: perrow@wattlebay.com.au p: 0491 570 156
Mira Perrow (Director) e: perrow@wattlebay.com.au p: 0491 570 157
Owen Halvey (General Manager) e: halvey@wattlebay.com.au p: 0491 570 158
Helen Halvey (General Manager) e: halvey@wattlebay.com.au p: 0491 570 159
Colin Danby (Training and Operations Manager) - e: danby@wattlebay.com.au p:0491 570 110
Colors
Look and feel

```html
<!DOCTYPE html>
<html lang="en">
<head>
<meta charset="utf-8">
<title>Wattle Bay Tourist Parks – Business Cards</title>
<link rel="stylesheet" href="https://fonts.googleapis.com/css2?family=Arimo:wght@400;700&display=swap">
<style>
  :root {
    --backdrop: #ece8e1;
    --card-white: #ffffff;
    --wave-green: #63b6a3;
    --mist: #e6f2f0;
    --back-teal: #3cb7c3;
    --name-grey: #5f6466;
    --text-white: #ffffff;
  }
  * { box-sizing: border-box; margin: 0; padding: 0; }
  html, body { width: 1200px; height: 911px; overflow: hidden; }
  body {
    background: var(--backdrop);
    position: relative;
    font-family: "Arimo", Arial, sans-serif;
  }
  .card {
    position: absolute;
    overflow: hidden;
    box-shadow: 0 10px 28px rgba(0,0,0,0.18);
  }

  /* Company name */
  .company-name {
    font-family: "Arimo", Arial, sans-serif;
    font-weight: 700;
    font-size: 26px;
    letter-spacing: 0;
    white-space: nowrap;
  }

  /* Front: portrait */
  .card-front {
    left: 120px; top: 120px;
    width: 400px; height: 640px;
    background: var(--card-white);
  }
  .front-brand {
    position: absolute;
    top: 100px; left: 0; right: 0;
    text-align: center;
    color: var(--name-grey);
  }
  .front-wave { position: absolute; left: 0; bottom: 0; width: 400px; height: 400px; }
  .contact {
    position: absolute;
    left: 34px; bottom: 92px;
    color: var(--text-white);
  }
  .contact-name { font-weight: 700; font-size: 22px; letter-spacing: 0.5px; text-transform: uppercase; }
  .contact-role { font-size: 15px; letter-spacing: 1px; text-transform: uppercase; margin: 4px 0 16px; }
  .contact-line { display: flex; align-items: center; gap: 10px; font-size: 15px; margin-top: 6px; letter-spacing: 0.3px; }
  .contact-line svg { width: 13px; height: 13px; flex: none; }

  /* Back: landscape */
  .card-back {
    left: 580px; top: 300px;
    width: 520px; height: 330px;
    background: var(--back-teal);
    color: var(--text-white);
  }
  .back-brand {
    position: absolute; top: 130px; left: 0; right: 0;
    text-align: center;
  }
  .back-brand .company-name { font-size: 30px; }
  .back-web {
    position: absolute; bottom: 40px; left: 0; right: 0;
    text-align: center;
    font-size: 15px; letter-spacing: 2px;
  }
</style>
</head>
<body>

  <section class="card card-front" aria-label="Business card front">
    <div class="front-brand">
      <span class="company-name">Wattle Bay Tourist Parks</span>
    </div>

    <svg class="front-wave" viewBox="0 0 400 400" aria-hidden="true">
      <path d="M0 140 C 90 95, 170 120, 240 190 C 300 250, 350 250, 400 235 L400 400 L0 400 Z" fill="var(--mist)"/>
      <path d="M0 160 C 90 115, 170 140, 235 210 C 295 270, 350 272, 400 258 L400 400 L0 400 Z" fill="var(--wave-green)"/>
    </svg>

    <div class="contact">
      <p class="contact-name">Neil Perrow</p>
      <p class="contact-role">Director</p>
      <p class="contact-line">
        <svg viewBox="0 0 24 24"><path fill="#fff" d="M6.6 10.8a15 15 0 0 0 6.6 6.6l2.2-2.2a1 1 0 0 1 1-.25 11.4 11.4 0 0 0 3.6.57 1 1 0 0 1 1 1V20a1 1 0 0 1-1 1A17 17 0 0 1 3 4a1 1 0 0 1 1-1h3.5a1 1 0 0 1 1 1c0 1.25.2 2.45.57 3.57a1 1 0 0 1-.25 1z"/></svg>
        <span>0491 570 156</span>
      </p>
      <p class="contact-line">
        <svg viewBox="0 0 24 24"><rect x="2" y="5" width="20" height="14" rx="2" fill="#fff"/><path d="M3 6l9 7 9-7" fill="none" stroke="var(--wave-green)" stroke-width="2"/></svg>
        <span>perrow@wattlebay.com.au</span>
      </p>
      <p class="contact-line">
        <svg viewBox="0 0 24 24"><circle cx="12" cy="12" r="10" fill="#fff"/><path d="M2 12h20M12 2c3 3 3 17 0 20M12 2c-3 3-3 17 0 20" fill="none" stroke="var(--wave-green)" stroke-width="1.5"/></svg>
        <span>www.wattlebay.com.au</span>
      </p>
    </div>
  </section>

  <section class="card card-back" aria-label="Business card back">
    <div class="back-brand">
      <span class="company-name">Wattle Bay Tourist Parks</span>
    </div>
    <p class="back-web">www.wattlebay.com.au</p>
  </section>

</body>
</html>
```